Meadow Paw Web Site

We have basically a start up business that I need help with. This project is just for the web site.

Our product is a frozen raw pet food that promotes weight control, less shedding, smaller stools and an overall better health. The product is in nugget form similar to what you would see in a steak shish kabob. I only share that with you in case you want to incorporate that in the design.

We have been in business for 17 years but all of our sales have been word of mouth. We are going to be launching an infomercial this summer and I need everything stated previously to be completed before we can launch the infomercial.

We need the following (6) pages:

Home:
This is where we need to have the ability to purchase our products. Our main goal is to get the consumer to purchase our product. We have our own shopping cart so we just need to allow for the insertion of that shopping cart.

Why Raw:
This will just be a page with 4-5 paragraphs and an embedded YouTube video.

How to Use:
We will need a page with a chart (4 Columns wide with 6 rows) as well as an embedded YouTube video.

Customer Success Stories:
Allow us to add these as we move forward. I need a placeholder for an image of the customers pet and a paragraph or two explaining the situation

Where to Buy:
- Online - Find a Retailer - Find a Local Distributor - Call to Order

Contact Us:
Copper Ridge Holdings, Inc.
2740 Copper Rd
Eagan, MN 55148
(800) xxx-xxxx

We need to provide links to our to be created... Facebook page, Twitter Account, Youtube Channel, Google circle, Blog
Updates

All, I have received many front page designs that look good.  Please notice in the brief that I need multiple pages built not just the home page.  

Thanks,

Dale

Reason: I need to see the rest of the pages. Thanks, Dale

Target Market(s)

Women between the ages of 30 & 60.

Industry/Entity Type

Shopping

```html
<!DOCTYPE html>
<html lang="en">
<head>
<meta charset="utf-8">
<title>Meadow Paw – Raw Dog Food</title>
<link href="https://fonts.googleapis.com/css2?family=Oxygen:wght@300;400;700&family=Gelasio:wght@700&display=swap" rel="stylesheet">
<style>
:root{
  --brown-dark:#2f1404;
  --brown:#5a2608;
  --rust:#8b3a17;
  --price:#b8622e;
  --gold:#f0b324;
  --gold-dark:#d99113;
  --text:#333;
  --muted:#7a7a7a;
  --line:#e3d9d2;
}
*{margin:0;padding:0;box-sizing:border-box}
html,body{width:778px;height:1200px;overflow:hidden;background:#fff}
body{font-family:"Oxygen",sans-serif;color:var(--text);position:relative}
.abs{position:absolute}

/* header */
.topbar{left:0;top:0;width:778px;height:70px;background:linear-gradient(#4a1e06,#6a2e0d)}
.navbar{left:0;top:70px;width:778px;height:37px;background:linear-gradient(#3a1805,#2a1003);border-top:1px solid #8a4a20}
.cart-tab{left:625px;top:0;width:83px;height:25px;background:#a96a3e;border-radius:0 0 6px 6px;color:#fff;font-size:10px;display:flex;align-items:center;justify-content:center;gap:5px}
.phone{left:590px;top:38px;color:#fff;font-size:16px;display:flex;align-items:center;gap:5px}
.nav a{position:absolute;top:84px;color:#fff;font-size:11px;text-decoration:none}
.nav .sep{position:absolute;top:70px;width:1px;height:37px;background:#5a2a10}
.brand{left:318px;top:70px;width:140px;height:37px;display:flex;align-items:center;justify-content:center;gap:6px}
.brand .mark{width:10px;height:10px;background:var(--gold)}
.brand span{font-size:15px;font-weight:400;color:#fff}

/* hero */
.hero{left:0;top:107px;width:778px;height:299px;background:linear-gradient(100deg,#c9b79f 0%,#7d8b45 25%,#bcae98 50%,#e6ddcf 75%,#d8c4ab 100%)}
.hero-title{left:0;top:216px;width:778px;text-align:center;font-family:"Gelasio",serif;color:#fff;font-size:28px;text-shadow:0 1px 3px rgba(0,0,0,.4)}
.hero-sub{left:0;top:253px;width:778px;text-align:center;font-family:"Gelasio",serif;color:#fff;font-size:16px;text-shadow:0 1px 3px rgba(0,0,0,.4)}
.dots{left:367px;top:387px;display:flex;gap:3px}
.dots i{width:9px;height:9px;border-radius:50%;background:#fff;display:block}

/* featured */
.section-title{font-size:15px;font-weight:400;color:var(--rust);text-transform:uppercase}
.products{left:73px;top:460px;width:633px;height:173px;border:1px solid var(--line);display:flex}
.product{flex:1;border-right:1px solid var(--line);padding:10px 16px 0 17px}
.product:last-child{border-right:none}
.product .pic{width:90px;height:78px;margin:0 auto 12px;border-radius:6px}
.product h3{font-size:11px;font-weight:400;color:#333}
.product p{font-size:7px;color:var(--muted);line-height:1.65;margin-top:2px}
.product .row{display:flex;justify-content:space-between;align-items:center;margin-top:5px}
.product .price{font-size:15px;color:var(--price);font-weight:700}

/* about */
.about-title{left:72px;top:660px;font-size:19px;font-weight:300;color:#222}
.about{left:73px;top:688px;width:395px;font-size:8.3px;color:var(--muted);line-height:1.65}
.about p{margin-bottom:5px}
.blog-title{left:72px;top:794px;font-size:16px;font-weight:400;color:var(--rust)}
.post .pic{position:absolute;width:72px;height:72px}
.post h4{position:absolute;font-size:11px;font-weight:400;color:#333}
.post p{position:absolute;width:112px;font-size:8.3px;color:var(--muted);line-height:1.6}
.btn{position:absolute;width:72px;height:20px;background:linear-gradient(#f7c23a,#e09a12);border-radius:2px;color:#fff;font-size:8px;text-align:center;line-height:20px}

/* stories */
.stories{left:502px;top:651px;width:204px;height:283px;border:1px solid #f1d6c3}
.ribbon-tail{top:660px;width:26px;height:30px;background:var(--gold-dark)}
.ribbon{left:502px;top:651px;width:204px;height:33px;background:linear-gradient(#f6bd2c,#e8a216);color:#fff;font-size:14px;padding:9px 0 0 18px}
.story .avatar{position:absolute;width:48px;height:48px;border-radius:50%;background:linear-gradient(#d8c8b8,#9a8a7a);border:3px solid #fff;box-shadow:0 1px 3px rgba(0,0,0,.35)}
.story p{position:absolute;width:124px;font-size:7.6px;font-style:italic;color:var(--muted);line-height:1.7}
.story b{position:absolute;font-size:7.5px;font-weight:400;color:#222}

/* footer */
.footer{left:0;top:982px;width:778px;height:176px;background:linear-gradient(#5a2507,#3e1904);border-top:1px dashed #a86a3e}
.footer-bottom{left:0;top:1158px;width:778px;height:42px;background:#3a1c10;color:#d8c2b0;font-size:8px;padding:16px 0 0 76px}
.fcol{position:absolute;top:1013px}
.fcol h5{font-size:12px;font-weight:400;color:#fff;margin-bottom:7px}
.fcol a{display:block;font-size:8.3px;color:#f1e3d6;text-decoration:none;line-height:15.5px}
.social{left:558px;top:1035px;display:flex;gap:4px}
.social i{display:block;width:24px;height:24px;border-radius:50%;background:#fff}
</style>
</head>
<body>

<header>
  <div class="abs topbar"></div>
  <div class="abs navbar"></div>
  <div class="abs cart-tab">
    <svg width="13" height="11" viewBox="0 0 13 11"><path d="M0 1h2.5l1.6 6h6.4l1.5-4.5H3.3" fill="none" stroke="#fff" stroke-width="1.1"/><circle cx="5" cy="9.5" r="1" fill="#fff"/><circle cx="9.5" cy="9.5" r="1" fill="#fff"/></svg>
    0 item
  </div>
  <div class="abs phone">
    <svg width="10" height="14" viewBox="0 0 10 14"><path d="M2 1l2 3-1.3 1.3c.6 1.8 1.5 3 3 4.3L7 8.3l2.5 2.3L8 13C4 12 1 7 1 2z" fill="#b2865e"/></svg>
    555.204.7731
  </div>
  <nav class="nav">
    <a style="left:96px">Home</a>
    <span class="sep" style="left:136px"></span>
    <a style="left:149px">Why RAW</a>
    <span class="sep" style="left:208px"></span>
    <a style="left:221px">How to Use</a>
    <a style="left:466px">Success Stories</a>
    <a style="left:560px">Where to Buy</a>
    <a style="left:644px">Contact us</a>
  </nav>
  <div class="abs brand"><i class="mark"></i><span>Meadow Paw</span></div>
</header>

<section>
  <div class="abs hero" role="img" aria-label="Photo of a woman kneeling to feed a brown and white dog from a green bowl"></div>
  <h1 class="abs hero-title">RAW FOOD CREATOR AND SELLER</h1>
  <div class="abs hero-sub">VESTIBULUM LIGULA AUGUE BIBENDUM</div>
  <div class="abs dots"><i></i><i></i><i></i><i></i></div>
</section>

<section>
  <h2 class="abs section-title" style="left:74px;top:433px">Featured Products</h2>
  <div class="abs products">
    <div class="product">
      <div class="pic" role="img" aria-label="Product photo of two raw food pouches" style="background:linear-gradient(135deg,#f2ece4,#b95d4a 60%,#e8dcc8)"></div>
      <h3>Product Name</h3>
      <p>Etiam eu urna Sed porta Suspendis se quam leo molestie sed</p>
      <div class="row"><span class="price">$25.99</span><svg width="18" height="16" viewBox="0 0 18 16"><path d="M0 1.5h3l2.2 9h8.5l2.2-7H4" fill="none" stroke="#999" stroke-width="1.3"/><circle cx="6.5" cy="13.8" r="1.4" fill="#999"/><circle cx="12.5" cy="13.8" r="1.4" fill="#999"/></svg></div>
    </div>
    <div class="product">
      <div class="pic" role="img" aria-label="Product photo of a clear bag of frozen nuggets" style="background:linear-gradient(135deg,#e4e8e6,#3e8a4e 55%,#cfd6d3)"></div>
      <h3>Product Name</h3>
      <p>Etiam eu urna Sed porta Suspendis se quam leo molestie sed</p>
      <div class="row"><span class="price">$25.99</span><svg width="18" height="16" viewBox="0 0 18 16"><path d="M0 1.5h3l2.2 9h8.5l2.2-7H4" fill="none" stroke="#999" stroke-width="1.3"/><circle cx="6.5" cy="13.8" r="1.4" fill="#999"/><circle cx="12.5" cy="13.8" r="1.4" fill="#999"/></svg></div>
    </div>
    <div class="product">
      <div class="pic" role="img" aria-label="Product photo of three wrapped raw food rolls" style="background:linear-gradient(135deg,#eee,#c2454a 50%,#ddd)"></div>
      <h3>Product Name</h3>
      <p>Etiam eu urna Sed porta Suspendis se quam leo molestie sed</p>
      <div class="row"><span class="price">$25.99</span><svg width="18" height="16" viewBox="0 0 18 16"><path d="M0 1.5h3l2.2 9h8.5l2.2-7H4" fill="none" stroke="#999" stroke-width="1.3"/><circle cx="6.5" cy="13.8" r="1.4" fill="#999"/><circle cx="12.5" cy="13.8" r="1.4" fill="#999"/></svg></div>
    </div>
    <div class="product">
      <div class="pic" role="img" aria-label="Product photo of a kibble bag with a dog" style="background:linear-gradient(135deg,#e9dcc0,#6a4a2a 55%,#cbb48c)"></div>
      <h3>Product Name</h3>
      <p>Etiam eu urna Sed porta Suspendis se quam leo molestie sed</p>
      <div class="row"><span class="price">$25.99</span><svg width="18" height="16" viewBox="0 0 18 16"><path d="M0 1.5h3l2.2 9h8.5l2.2-7H4" fill="none" stroke="#999" stroke-width="1.3"/><circle cx="6.5" cy="13.8" r="1.4" fill="#999"/><circle cx="12.5" cy="13.8" r="1.4" fill="#999"/></svg></div>
    </div>
  </div>
</section>

<section>
  <h2 class="abs about-title">Little About Our Company</h2>
  <div class="abs about">
    <p>Mauris vel lacus vitae felis vestibulum volutpat Etiam est nunc venenatis in tristique eu imperdiet ac nisl Cum sociis natoque penatibus et magnis dis parturient montes nascetur ridiculus mus In iaculis facilisis massa Etiam eu urna Sed porta Suspendisse quam leo molestie sed luctus quis feugiat in pede</p>
    <p>Mauris vel lacus vitae felis vestibulum volutpat Etiam est nunc venenatis in tristique eu imperdiet ac nisl Cum sociis natoque penatibus et magnis dis parturient montes nascetur ridiculus mus In iaculis facilisis massa Etiam eu urna Sed porta Suspendisse quam leo molestie sed luctus quis feugiat in pede</p>
  </div>

  <h2 class="abs blog-title">Recent Blog Post</h2>
  <div class="post">
    <div class="pic" style="left:72px;top:823px;background:linear-gradient(135deg,#e8d6b0,#f4f0ea 50%,#3a3030)" role="img" aria-label="Photo of two puppies eating from a red bowl"></div>
    <h4 style="left:152px;top:822px">Eu imperdiet nisl</h4>
    <p style="left:152px;top:838px">Cum sociis natoque penati-bus et magnis dis parturient montes nascetur ridiculus mus In iaculis</p>
    <span class="btn" style="left:151px;top:897px">READ MORE</span>
  </div>
  <div class="post">
    <div class="pic" style="left:274px;top:823px;background:linear-gradient(135deg,#6a8aa8,#e8e2d6 55%,#c8a878)" role="img" aria-label="Photo of a boy sitting with a light coloured dog"></div>
    <h4 style="left:354px;top:822px">Eu imperdiet nisl</h4>
    <p style="left:354px;top:838px">Cum sociis natoque penati-bus et magnis dis parturient montes nascetur ridiculus mus In iaculis</p>
    <span class="btn" style="left:353px;top:898px">READ MORE</span>
  </div>
</section>

<aside>
  <div class="abs stories"></div>
  <div class="abs ribbon-tail" style="left:480px;clip-path:polygon(0 0,100% 0,100% 100%,0 100%,35% 50%)"></div>
  <div class="abs ribbon-tail" style="left:702px;clip-path:polygon(0 0,100% 0,65% 50%,100% 100%,0 100%)"></div>
  <div class="abs ribbon">Success Stories</div>
  <div class="story">
    <div class="avatar" style="left:516px;top:697px" role="img" aria-label="Customer portrait"></div>
    <p style="left:570px;top:697px">Vestibulum ligula augue bibendum accumsan vestibulum ut commodo a mi Morbi ornare gravida elit Inte-ger Praesent elementum elit at</p>
    <b style="left:571px;top:752px">By Author Name</b>
  </div>
  <div class="story">
    <div class="avatar" style="left:516px;top:775px" role="img" aria-label="Customer portrait"></div>
    <p style="left:570px;top:778px">Vestibulum ligula augue bibendum accumsan vestibulum ut commodo a mi Morbi ornare gravida</p>
    <b style="left:571px;top:820px">By Author Name</b>
  </div>
  <div class="story">
    <div class="avatar" style="left:516px;top:843px" role="img" aria-label="Customer portrait"></div>
    <p style="left:570px;top:844px">Morbi eget arcu Morbi porta libero id ullamcorper nonummy nibh ligula pulvinar metus eget consect-etuer augue nisi quis lacus</p>
    <b style="left:571px;top:899px">By Author Name</b>
  </div>
</aside>

<footer>
  <div class="abs footer"></div>
  <div class="fcol" style="left:82px"><h5>COMPANY</h5><a>Home</a><a>Why RAW</a><a>How to Use</a><a>Success Stories</a><a>Where to Buy</a><a>Contact us</a></div>
  <div class="fcol" style="left:193px"><h5>PRODUCTS</h5><a>Aliquam nec</a><a>erat at purus cursus</a><a>interdum Vesti</a><a>bulum ligula</a><a>augue bibend</a></div>
  <div class="fcol" style="left:319px"><h5>SUBLINKS</h5><a>Aliquam nec</a><a>erat at purus cursus</a><a>interdum Vesti</a><a>bulum ligula</a><a>augue bibend</a></div>
  <div class="fcol" style="left:445px"><h5>SUPPORT</h5><a>Aliquam nec</a><a>erat at purus cursus</a><a>interdum Vesti</a><a>bulum ligula</a><a>augue bibend</a></div>
  <div class="fcol" style="left:560px"><h5>GET IN TOUCH</h5></div>
  <div class="abs social" aria-label="Social media links"><i></i><i></i><i></i><i></i><i></i></div>
  <div class="abs footer-bottom">© 2014 Company Name.&nbsp; All right reserved.&nbsp; Term of Use</div>
</footer>

</body>
</html>
```